BrindleStaffing Business Card Design

We are a staffing company finding positions for dedicated nurses and physicians.

Target Market(s)

Business Professionals

Industry/Entity Type

Staffing

Contact Information for Business Card

Gordon Pratley
Chairman
417 39th Avenue South
SAINT PETERSBURG FL 33712
813-555-4172 Mobile
813-555-8036 Fax
gpratley@brindlestaffing.com
www.brindlestaffing.com

Font styles to use
Sans Serif

Colors
fbee3e
f04a50
f37122

Requirements
Must have
• Logo Attached, see colors below. We'd like to see Yellow, Orange and Red.

```html
<!DOCTYPE html>
<html lang="en">
<head>
<meta charset="utf-8">
<title>BrindleStaffing Business Card</title>
<link href="https://fonts.googleapis.com/css2?family=Questrial&family=Roboto:wght@400;700&display=swap" rel="stylesheet">
<style>
  :root {
    --page-bg: #2a2a2a;
    --card-white: #ffffff;
    --brand-red: #f04a50;
    --brand-orange: #f37122;
    --brand-yellow: #fbee3e;
    --text-grey: #4a4a4a;
    --white: #ffffff;
  }
  * { margin: 0; padding: 0; box-sizing: border-box; }
  html, body {
    width: 1125px;
    height: 1200px;
    overflow: hidden;
    background: var(--page-bg);
  }
  .canvas {
    position: relative;
    width: 1125px;
    height: 1200px;
  }
  .card {
    position: absolute;
    left: 150px;
    width: 826px;
    height: 471px;
    overflow: hidden;
  }
  .card-front { top: 98px; background: var(--card-white); }
  .card-back { top: 630px; background: var(--brand-orange); }

  .wordmark {
    position: absolute;
    font-family: 'Roboto', sans-serif;
    font-weight: 700;
    letter-spacing: -1px;
    line-height: 1;
    white-space: nowrap;
  }
  .card-front .brand-line {
    position: absolute;
    left: 44px;
    top: 68px;
    display: flex;
    align-items: center;
  }
  .card-front .wordmark {
    position: static;
    font-size: 49px;
    color: var(--brand-red);
  }
  .brand-dot {
    width: 16px;
    height: 16px;
    border-radius: 50%;
    background: var(--brand-yellow);
    margin-left: 8px;
    flex: none;
  }

  .address {
    position: absolute;
    left: 44px;
    top: 218px;
    font-family: 'Roboto', sans-serif;
    font-style: normal;
    font-size: 19.5px;
    line-height: 25px;
    color: var(--text-grey);
  }
  .contacts {
    position: absolute;
    left: 44px;
    top: 314px;
    list-style: none;
    font-family: 'Roboto', sans-serif;
    font-size: 19.5px;
    color: var(--text-grey);
  }
  .contacts li {
    display: flex;
    align-items: center;
    height: 26.3px;
  }
  .contacts svg {
    width: 20px;
    height: 20px;
    margin-right: 13px;
    flex: none;
  }

  .cross-bar { position: absolute; background: var(--brand-red); }
  .cross-vertical { left: 528px; top: 69px; width: 153px; height: 361px; }
  .cross-horizontal { left: 415px; top: 179px; width: 381px; height: 143px; }

  .person {
    position: absolute;
    left: 415px;
    top: 216px;
    width: 381px;
    text-align: center;
    font-family: 'Questrial', sans-serif;
    color: var(--white);
  }
  .person-name { font-size: 29px; letter-spacing: 1px; line-height: 1.2; }
  .person-title { font-size: 18.5px; letter-spacing: 1.5px; margin-top: 4px; }

  .back-pattern {
    position: absolute;
    inset: 0;
    background: linear-gradient(135deg, var(--brand-orange) 0%, #f4792c 55%, var(--brand-orange) 100%);
  }
  .card-back .brand-block {
    position: absolute;
    right: 44px;
    top: 352px;
    text-align: right;
  }
  .card-back .wordmark {
    position: static;
    font-size: 42px;
    color: var(--white);
  }
  .card-back .web {
    margin-top: 10px;
    font-family: 'Roboto', sans-serif;
    font-size: 18.5px;
    letter-spacing: 3px;
    color: var(--white);
  }
</style>
</head>
<body>
<main class="canvas">

  <section class="card card-front" aria-label="Card front">
    <div class="brand-line">
      <div class="wordmark">BrindleStaffing</div>
      <span class="brand-dot" aria-hidden="true"></span>
    </div>

    <address class="address">
      417 39th Avenue<br>
      South, SAINT<br>
      PETERSBURG FL 33712
    </address>

    <ul class="contacts">
      <li>
        <svg viewBox="0 0 20 20" aria-hidden="true"><rect x="5" y="1" width="10" height="18" rx="2" fill="var(--brand-red)"/><rect x="7" y="4" width="6" height="10" fill="#fff"/></svg>
        813-555-4172
      </li>
      <li>
        <svg viewBox="0 0 20 20" aria-hidden="true"><rect x="5" y="3" width="10" height="6" fill="var(--brand-red)"/><rect x="1" y="9" width="18" height="8" rx="1.5" fill="var(--brand-red)"/><rect x="5" y="12" width="10" height="2" fill="#fff"/></svg>
        813-555-8036
      </li>
      <li>
        <svg viewBox="0 0 20 20" aria-hidden="true"><rect x="1" y="5" width="18" height="11" fill="var(--brand-red)"/><path d="M1.5 5.5 L10 12 L18.5 5.5" stroke="#fff" stroke-width="1.5" fill="none"/></svg>
        gpratley@brindlestaffing.com
      </li>
      <li>
        <svg viewBox="0 0 20 20" aria-hidden="true"><circle cx="10" cy="10" r="8.5" fill="var(--brand-red)"/><path d="M6 5 Q9 7 8 10 Q6 12 7 15 M12 4 Q11 8 14 9 Q16 11 14 15" stroke="#fff" stroke-width="1.6" fill="none"/></svg>
        www.brindlestaffing.com
      </li>
    </ul>

    <div class="cross-bar cross-vertical"></div>
    <div class="cross-bar cross-horizontal"></div>
    <div class="person">
      <div class="person-name">Gordon Pratley</div>
      <div class="person-title">Chairman</div>
    </div>
  </section>

  <section class="card card-back" aria-label="Card back">
    <div class="back-pattern" role="img" aria-label="Soft pattern of light orange dots scattered across the orange background"></div>
    <div class="brand-block">
      <div class="wordmark">BrindleStaffing</div>
      <div class="web">www.brindlestaffing.com</div>
    </div>
  </section>

</main>
</body>
</html>
```